Presentation Brochure and Sample Box Design for Kovo Slate

Kovo Slate is a colour coated solid aluminium panel that our company supplies to the signage and building cladding industries.
We require an, A4 double-sided folding brochure (swatch book) that folds 3 ways, opening once and then a second time to lay out 3 pages flat.

There should be a front and back cover.

The inside cover should be reserved with text blocks for written information about the panel.

The opposite page on the right when you first open the brochure should have all our Matte PVDF 2mm colours which you will find in the attached PDF of colour swatches and details.

When the brochure is folded out a second time, showing all three inside pages flat, the two inside pages on the right (next to the inside cover with the written information) should show all our FEVE Gloss 1.6mm colours which you will also find in the attached PDF colour book.

This brochure should have a modern and professional feel suitable for presenting to architects and designers.

We also require a box design to contain aluminium samples of all the colours in the range.

Please refer to the template attached for the box dimensions and layout.

The box should tie in with the brochure as a complete package with a modern and professional look suitable for presenting to architects and designers.

Finally we require a small label sticker to be stuck on the back of each sample. On the sticker should be the Kovo Slate logo, a space to put the product code for the sample colour and the phone number 1300 584 362.

To summarise, this package project includes:
1 tri-folding A4 brochure,
1 sample box package design,
1 sample sticker label.

This is our signature new product that we will be marketing to signage installers to create coloured and printed aluminium signs. We are also looking to move further into the building and architectural market place with this product.

Please refer to the attachments for the Kovo Slate logo - the colour swatch book and template for the sample box.
The Kovo Slate logo can be shown in White, Black or Silver.

Target Market(s)

Architects, interior designers, builders and signage installers.

Font styles to use
Serif
Sans Serif

Requirements
Must have
• A modern, neat and professional upmarket look suitable for presenting to architects.
Nice to have
• A slick and classy look that makes you want to take home the box or brochure even if you're not interested in the product.
Should not have
• A cheap, untidy, low market look with too many colours.

```html
<!DOCTYPE html>
<html lang="en">
<head>
<meta charset="utf-8">
<title>Kovo Slate – Tri-fold Swatch Brochure</title>
<link rel="stylesheet" href="https://fonts.googleapis.com/css2?family=Montserrat:wght@200;400;500;600;700;800&display=swap">
<style>
:root{
  --ink:#121212;
  --paper:#ffffff;
  --mist:#f1f1f1;
  --stage:#d9d9d9;
  --rule:#cfcfcf;
  --muted:#9a9a9a;
  --alert:#d8242a;
  --sky-top:#d8d0e6;
  --sky-mid:#a9b2d4;
  --house:#56648f;
  --drive:#a7aec8;
}
*{box-sizing:border-box;margin:0;padding:0}
html,body{width:1200px;height:2326px;overflow:hidden}
body{background:var(--stage);font-family:"Montserrat",sans-serif;color:var(--ink);position:relative}

.side-label{position:absolute;left:45px;font:500 20px/1 "Montserrat",sans-serif;letter-spacing:3px;transform:translate(-50%,-50%) rotate(-90deg);white-space:nowrap}

.spread{position:absolute;left:90px;width:1080px;height:750px;display:grid;grid-template-columns:repeat(3,360px);border-bottom:5px solid var(--ink);box-shadow:0 2px 8px rgba(0,0,0,.18)}
.spread--outside{top:330px}
.spread--inside{top:1240px}

.panel{position:relative;height:100%;overflow:hidden;background:var(--paper)}
.panel--soft{background:linear-gradient(180deg,var(--paper),var(--mist))}
.panel--black{background:var(--ink);color:var(--paper)}

.range-head{text-align:center;padding-top:16px}
.range-head .kicker{display:block;font:200 17px/1 "Montserrat",sans-serif;color:var(--muted);letter-spacing:-.2px}
.range-head .title{display:block;margin:4px auto 0;font:500 15px/1.3 "Montserrat",sans-serif;width:300px;background:linear-gradient(90deg,transparent,#e6e6e6 20%,#e6e6e6 80%,transparent)}

.wordmark{font:500 38px/1 "Montserrat",sans-serif;letter-spacing:2px;white-space:nowrap;text-align:center}

.swatches{display:flex;flex-direction:column;justify-content:space-between;padding:0 14px}
.sw{display:grid;grid-template-columns:42px 42px 1fr;gap:6px;align-items:center}
.chip{height:26px;background:var(--c);color:var(--paper);font:600 4.6px/1.15 "Montserrat",sans-serif;display:flex;align-items:flex-end;justify-content:center;text-align:center;padding-bottom:3px}
.chip.lt{color:var(--ink);box-shadow:inset 0 0 0 .5px var(--rule)}
.under{height:26px;background:var(--paper);box-shadow:0 0 2px rgba(0,0,0,.25);font:600 4.4px/1.15 "Montserrat",sans-serif;display:flex;align-items:center;justify-content:center;text-align:center}
.spec{display:grid;grid-template-columns:1.3fr 1.2fr 1fr .8fr;font:400 4.2px/1.45 "Montserrat",sans-serif;text-align:center}
.spec b{font-weight:700;background:#ececec;border-top:.8px solid var(--rule)}
.spec i{font-style:normal;color:#555}
.spec .note{grid-column:1/-1;text-align:left;padding-left:6px;color:var(--alert);font-weight:700;font-style:italic}
.swatches--tight .chip,.swatches--tight .under{height:21px}

.pvdf-list{height:655px;padding-top:10px}
.contact{position:absolute;left:0;right:0;text-align:center}
.pill{display:inline-block;border-radius:14px;font:800 15px/28px "Montserrat",sans-serif;letter-spacing:1px;padding:0 18px}
.pill--light{background:var(--paper);color:var(--ink)}
.pill--dark{background:var(--ink);color:var(--paper)}
.web{display:block;font:500 11px/1 "Montserrat",sans-serif;letter-spacing:3.4px;margin-top:9px}
.address{font:400 11px/1.35 "Montserrat",sans-serif;margin:10px 0 14px}

.cover-art{position:absolute;inset:0}
.cover-logo{position:absolute;top:105px;left:30px;right:0;color:var(--ink)}
.cover-contact{top:676px}

.intro{position:absolute;top:0;left:0;width:360px;height:290px}
.intro-copy{position:absolute;top:18px;left:14px;right:14px;color:var(--paper);font:400 6.4px/1.55 "Montserrat",sans-serif}
.intro-copy p+p{margin-top:8px}
.inside-logo{position:absolute;top:300px;left:0;right:0}
.inside-head{position:absolute;top:345px;left:0;right:0;padding-top:0}
.gloss-list{position:absolute;top:400px;left:0;right:0;height:340px}
.mid-list{height:100%;padding-top:12px;padding-bottom:10px}
.right-top{height:340px;padding-top:12px}
.metal-head{text-align:center;font:500 15px/1.3 "Montserrat",sans-serif;margin:8px auto 6px;width:300px;background:linear-gradient(90deg,transparent,#e6e6e6 20%,#e6e6e6 80%,transparent)}
.right-bottom{height:360px}
</style>
</head>
<body>

<div class="side-label" style="top:705px">OUTSIDE</div>
<div class="side-label" style="top:1615px">INSIDE</div>

<section class="spread spread--outside">

  <div class="panel">
    <h2 class="range-head"><span class="kicker">COLOUR COATED SOLID ALUMINIUM</span><span class="title">PVDF MATTE 2MM</span></h2>
    <div class="swatches pvdf-list">
      <div class="sw"><span class="chip lt" style="--c:#ffffff">PVDF MATTE<br>WHITE</span><span class="under">MATTE WHITE<br>UNDERCOAT</span><div class="spec"><b>REFERENCE</b><b>SIZE</b><b>THICKNESS</b><b>FOLDABLE</b><i>KSPV01-1224-2</i><i>2400 X 1220mm</i><i>2mm</i><i>Yes</i></div></div>
      <div class="sw"><span class="chip" style="--c:#111111">PVDF MATTE<br>BLACK</span><span class="under">MATTE WHITE<br>UNDERCOAT</span><div class="spec"><b>REFERENCE</b><b>SIZE</b><b>THICKNESS</b><b>FOLDABLE</b><i>KSPV02-1224-2</i><i>2400 X 1220mm</i><i>2mm</i><i>Yes</i></div></div>
      <div class="sw"><span class="chip" style="--c:#d62b2b">PVDF MATTE<br>RED</span><span class="under">MATTE WHITE<br>UNDERCOAT</span><div class="spec"><b>REFERENCE</b><b>SIZE</b><b>THICKNESS</b><b>FOLDABLE</b><i>KSPV03-1224-2</i><i>2400 X 1220mm</i><i>2mm</i><i>Yes</i><span class="note">*CHECK AVAILABILITY</span></div></div>
      <div class="sw"><span class="chip" style="--c:#2a3a8c">PVDF MATTE<br>REFLEX BLUE</span><span class="under">MATTE WHITE<br>UNDERCOAT</span><div class="spec"><b>REFERENCE</b><b>SIZE</b><b>THICKNESS</b><b>FOLDABLE</b><i>KSPV04-1224-2</i><i>2400 X 1220mm</i><i>2mm</i><i>Yes</i><span class="note">*CHECK AVAILABILITY</span></div></div>
      <div class="sw"><span class="chip" style="--c:#ee6a2a">PVDF MATTE<br>ORANGE</span><span class="under">MATTE WHITE<br>UNDERCOAT</span><div class="spec"><b>REFERENCE</b><b>SIZE</b><b>THICKNESS</b><b>FOLDABLE</b><i>KSPV05-1224-2</i><i>2400 X 1220mm</i><i>2mm</i><i>Yes</i><span class="note">*CHECK AVAILABILITY</span></div></div>
      <div class="sw"><span class="chip" style="--c:#1e2a55">PVDF MATTE<br>NAVY BLUE</span><span class="under">MATTE WHITE<br>UNDERCOAT</span><div class="spec"><b>REFERENCE</b><b>SIZE</b><b>THICKNESS</b><b>FOLDABLE</b><i>KSPV06-1224-2</i><i>2400 X 1220mm</i><i>2mm</i><i>Yes</i><span class="note">*CHECK AVAILABILITY</span></div></div>
      <div class="sw"><span class="chip" style="--c:#2c3670">PVDF MATTE<br>GALAXY</span><span class="under">MATTE WHITE<br>UNDERCOAT</span><div class="spec"><b>REFERENCE</b><b>SIZE</b><b>THICKNESS</b><b>FOLDABLE</b><i>KSPV07-1224-2</i><i>2400 X 1220mm</i><i>2mm</i><i>Yes</i><span class="note">*CHECK AVAILABILITY</span></div></div>
      <div class="sw"><span class="chip lt" style="--c:#e6d7a0">PVDF MATTE<br>IVORY</span><span class="under">MATTE WHITE<br>UNDERCOAT</span><div class="spec"><b>REFERENCE</b><b>SIZE</b><b>THICKNESS</b><b>FOLDABLE</b><i>KSPV08-1224-2</i><i>2400 X 1220mm</i><i>2mm</i><i>Yes</i><span class="note">*CHECK AVAILABILITY</span></div></div>
      <div class="sw"><span class="chip" style="--c:#f0b21a">PVDF MATTE<br>MUSTARD</span><span class="under">MATTE WHITE<br>UNDERCOAT</span><div class="spec"><b>REFERENCE</b><b>SIZE</b><b>THICKNESS</b><b>FOLDABLE</b><i>KSPV09-1224-2</i><i>2400 X 1220mm</i><i>2mm</i><i>Yes</i><span class="note">*CHECK AVAILABILITY</span></div></div>
      <div class="sw"><span class="chip" style="--c:#b51e3a">PVDF MATTE<br>PLUM RED</span><span class="under">MATTE WHITE<br>UNDERCOAT</span><div class="spec"><b>REFERENCE</b><b>SIZE</b><b>THICKNESS</b><b>FOLDABLE</b><i>KSPV10-1224-2</i><i>2400 X 1220mm</i><i>2mm</i><i>Yes</i><span class="note">*CHECK AVAILABILITY</span></div></div>
      <div class="sw"><span class="chip" style="--c:#4a4f55">PVDF MATTE<br>STEEL GREY</span><span class="under">MATTE WHITE<br>UNDERCOAT</span><div class="spec"><b>REFERENCE</b><b>SIZE</b><b>THICKNESS</b><b>FOLDABLE</b><i>KSPV11-1224-2</i><i>2400 X 1220mm</i><i>2mm</i><i>Yes</i><span class="note">*CHECK AVAILABILITY</span></div></div>
      <div class="sw"><span class="chip" style="--c:#5f6670">PVDF MATTE<br>IRON GREY</span><span class="under">MATTE WHITE<br>UNDERCOAT</span><div class="spec"><b>REFERENCE</b><b>SIZE</b><b>THICKNESS</b><b>FOLDABLE</b><i>KSPV12-1224-2</i><i>2400 X 1220mm</i><i>2mm</i><i>Yes</i><span class="note">*CHECK AVAILABILITY</span></div></div>
      <div class="sw"><span class="chip" style="--c:#9a9ea3">PVDF MATTE<br>WARM GREY</span><span class="under">MATTE WHITE<br>UNDERCOAT</span><div class="spec"><b>REFERENCE</b><b>SIZE</b><b>THICKNESS</b><b>FOLDABLE</b><i>KSPV13-1224-2</i><i>2400 X 1220mm</i><i>2mm</i><i>Yes</i><span class="note">*CHECK AVAILABILITY</span></div></div>
      <div class="sw"><span class="chip" style="--c:#a8aaab">PVDF MATTE<br>SMOKEY GREY</span><span class="under">MATTE WHITE<br>UNDERCOAT</span><div class="spec"><b>REFERENCE</b><b>SIZE</b><b>THICKNESS</b><b>FOLDABLE</b><i>KSPV14-1224-2</i><i>2400 X 1220mm</i><i>2mm</i><i>Yes</i><span class="note">*CHECK AVAILABILITY</span></div></div>
      <div class="sw"><span class="chip lt" style="--c:#d8d2bf">PVDF MATTE<br>CREAM</span><span class="under">MATTE WHITE<br>UNDERCOAT</span><div class="spec"><b>REFERENCE</b><b>SIZE</b><b>THICKNESS</b><b>FOLDABLE</b><i>KSPV15-1224-2</i><i>2400 X 1220mm</i><i>2mm</i><i>Yes</i><span class="note">*CHECK AVAILABILITY</span></div></div>
      <div class="sw"><span class="chip" style="--c:#b8b8b8">PVDF METALLIC<br>SILVER</span><span class="under">MATTE WHITE<br>UNDERCOAT</span><div class="spec"><b>REFERENCE</b><b>SIZE</b><b>THICKNESS</b><b>FOLDABLE</b><i>KSPV16-1224-2</i><i>2400 X 1220mm</i><i>2mm</i><i>Yes</i><span class="note">*CHECK AVAILABILITY</span></div></div>
      <div class="sw"><span class="chip" style="--c:#555555">PVDF METALLIC<br>CHARCOAL</span><span class="under">MATTE WHITE<br>UNDERCOAT</span><div class="spec"><b>REFERENCE</b><b>SIZE</b><b>THICKNESS</b><b>FOLDABLE</b><i>KSPV17-1224-2</i><i>2400 X 1220mm</i><i>2mm</i><i>Yes</i><span class="note">*CHECK AVAILABILITY</span></div></div>
      <div class="sw"><span class="chip" style="--c:#c9a55a">PVDF METALLIC<br>GOLD</span><span class="under">MATTE WHITE<br>UNDERCOAT</span><div class="spec"><b>REFERENCE</b><b>SIZE</b><b>THICKNESS</b><b>FOLDABLE</b><i>KSPV18-1224-2</i><i>2400 X 1220mm</i><i>2mm</i><i>Yes</i><span class="note">*CHECK AVAILABILITY</span></div></div>
      <div class="sw"><span class="chip" style="--c:#e2c21a">PVDF METALLIC<br>YELLOW</span><span class="under">MATTE WHITE<br>UNDERCOAT</span><div class="spec"><b>REFERENCE</b><b>SIZE</b><b>THICKNESS</b><b>FOLDABLE</b><i>KSPV19-1224-2</i><i>2400 X 1220mm</i><i>2mm</i><i>Yes</i><span class="note">*CHECK AVAILABILITY</span></div></div>
      <div class="sw"><span class="chip" style="--c:#1e63b0">PVDF METALLIC<br>BLUE</span><span class="under">MATTE WHITE<br>UNDERCOAT</span><div class="spec"><b>REFERENCE</b><b>SIZE</b><b>THICKNESS</b><b>FOLDABLE</b><i>KSPV20-1224-2</i><i>2400 X 1220mm</i><i>2mm</i><i>Yes</i><span class="note">*CHECK AVAILABILITY</span></div></div>
    </div>
  </div>

  <div class="panel panel--black">
    <div class="contact" style="top:240px">
      <div class="wordmark" style="color:var(--paper)">KOVO SLATE</div>
      <svg width="34" height="44" viewBox="0 0 34 44" style="margin-top:40px" aria-hidden="true">
        <path d="M17 2C9 2 3 8 3 16c0 10 14 26 14 26s14-16 14-26C31 8 25 2 17 2z" fill="#fff"/>
        <circle cx="17" cy="16" r="9" fill="none" stroke="#121212" stroke-width="1.6"/>
        <path d="M12 18l5-5 5 5M13.5 17v4h7v-4" fill="none" stroke="#121212" stroke-width="1.4"/>
      </svg>
      <p class="address">1-2 Lorem ipsum St, lorem ipsum 1234,<br>Australia</p>
      <span class="pill pill--light">CALL US TODAY! 123 456 7890</span>
      <span class="web">www.webaddress.com</span>
    </div>
  </div>

  <div class="panel">
    <svg class="cover-art" width="360" height="750" viewBox="0 0 360 750">
      <defs>
        <linearGradient id="homeTones" x1="0" y1="0" x2="0" y2="1">
          <stop offset="0" stop-color="var(--sky-top)"/>
          <stop offset=".3" stop-color="var(--sky-mid)"/>
          <stop offset=".62" stop-color="var(--house)"/>
          <stop offset="1" stop-color="var(--drive)"/>
        </linearGradient>
        <linearGradient id="sheen" x1="0" y1="0" x2="1" y2="0">
          <stop offset="0" stop-color="#ffffff"/>
          <stop offset="1" stop-color="#dcdcdc"/>
        </linearGradient>
      </defs>
      <path d="M0 0H360V690C120 620 -20 420 0 0z" fill="url(#sheen)" opacity=".6"/>
      <path d="M6 0C-38 250 10 500 360 664L360 636C42 486 0 262 36 0z" fill="#121212"/>
      <path d="M46 0C10 262 52 482 360 624V0z" fill="url(#homeTones)" role="img" aria-label="Photograph of a modern two-storey home with double garage at dusk"/>
    </svg>
    <div class="wordmark cover-logo">KOVO SLATE</div>
    <div class="contact cover-contact">
      <span class="pill pill--dark">CALL US TODAY! 123 456 7890</span>
      <span class="web">www.webaddress.com</span>
    </div>
  </div>
</section>

<section class="spread spread--inside">

  <div class="panel panel--soft">
    <svg class="intro" viewBox="0 0 360 290" aria-hidden="true">
      <path d="M0 0H360V215Q180 300 0 215z" fill="#121212"/>
      <circle cx="180" cy="266" r="8" fill="#fff"/>
      <path d="M176 264l4 4 4-4" fill="none" stroke="#121212" stroke-width="1.5"/>
    </svg>
    <div class="intro-copy">
      <p>Lorem Ipsum is simply dummy text of the printing and typesetting industry. Lorem Ipsum has been the industry's standard dummy text ever since the 1500s, when an unknown printer took a galley of type and scrambled it to make a type specimen book. It has survived not only five centuries, but also the leap into electronic typesetting, remaining essentially unchanged. It was popularised in the 1960s with the release of Letraset sheets containing Lorem Ipsum passages, and more recently with desktop publishing software like Aldus PageMaker including versions of Lorem Ipsum.</p>
      <p>Lorem Ipsum is simply dummy text of the printing and typesetting industry. Lorem Ipsum has been the industry's standard dummy text ever since the 1500s, when an unknown printer took a galley of type and scrambled it to make a type specimen book. It has survived not only five centuries, but also the leap into electronic typesetting, remaining essentially unchanged.</p>
      <p>Lorem Ipsum is simply dummy text of the printing and typesetting industry. Lorem Ipsum has been the industry's standard dummy text ever since the 1500s, when an unknown printer took a galley of type and scrambled it to make a type specimen book.</p>
    </div>
    <div class="wordmark inside-logo">KOVO SLATE</div>
    <h2 class="range-head inside-head"><span class="kicker">COLOUR COATED SOLID ALUMINIUM</span><span class="title">FEVE GLOSS 1.6MM</span></h2>
    <div class="swatches swatches--tight gloss-list">
      <div class="sw"><span class="chip lt" style="--c:#ffffff">FEVE GLOSS<br>WHITE</span><span class="under">MATTE WHITE<br>UNDERCOAT</span><div class="spec"><b>REFERENCE</b><b>SIZE</b><b>THICKNESS</b><b>FOLDABLE</b><i>KSFG01-1224-16</i><i>2400 X 1220mm</i><i>1.6mm</i><i>Yes</i></div></div>
      <div class="sw"><span class="chip" style="--c:#111111">FEVE GLOSS<br>BLACK</span><span class="under">MATTE WHITE<br>UNDERCOAT</span><div class="spec"><b>REFERENCE</b><b>SIZE</b><b>THICKNESS</b><b>FOLDABLE</b><i>KSFG02-1224-16</i><i>2400 X 1220mm</i><i>1.6mm</i><i>Yes</i></div></div>
      <div class="sw"><span class="chip" style="--c:#d62b2b">FEVE GLOSS<br>RED</span><span class="under">MATTE WHITE<br>UNDERCOAT</span><div class="spec"><b>REFERENCE</b><b>SIZE</b><b>THICKNESS</b><b>FOLDABLE</b><i>KSFG03-1224-16</i><i>2400 X 1220mm</i><i>1.6mm</i><i>Yes</i></div></div>
      <div class="sw"><span class="chip lt" style="--c:#f0e020">FEVE GLOSS<br>YELLOW</span><span class="under">MATTE WHITE<br>UNDERCOAT</span><div class="spec"><b>REFERENCE</b><b>SIZE</b><b>THICKNESS</b><b>FOLDABLE</b><i>KSFG04-1224-16</i><i>2400 X 1220mm</i><i>1.6mm</i><i>Yes</i></div></div>
      <div class="sw"><span class="chip" style="--c:#1a7ac0">FEVE GLOSS<br>PROCESS BLUE</span><span class="under">MATTE WHITE<br>UNDERCOAT</span><div class="spec"><b>REFERENCE</b><b>SIZE</b><b>THICKNESS</b><b>FOLDABLE</b><i>KSFG05-1224-16</i><i>2400 X 1220mm</i><i>1.6mm</i><i>Yes</i></div></div>
      <div class="sw"><span class="chip" style="--c:#1f3c96">FEVE GLOSS<br>REFLEX BLUE</span><span class="under">MATTE WHITE<br>UNDERCOAT</span><div class="spec"><b>REFERENCE</b><b>SIZE</b><b>THICKNESS</b><b>FOLDABLE</b><i>KSFG06-1224-16</i><i>2400 X 1220mm</i><i>1.6mm</i><i>Yes</i></div></div>
      <div class="sw"><span class="chip" style="--c:#1e4a2a">FEVE GLOSS<br>FOREST GREEN</span><span class="under">MATTE WHITE<br>UNDERCOAT</span><div class="spec"><b>REFERENCE</b><b>SIZE</b><b>THICKNESS</b><b>FOLDABLE</b><i>KSFG07-1224-16</i><i>2400 X 1220mm</i><i>1.6mm</i><i>Yes</i></div></div>
      <div class="sw"><span class="chip" style="--c:#8a2323">FEVE GLOSS<br>HERITAGE RED</span><span class="under">MATTE WHITE<br>UNDERCOAT</span><div class="spec"><b>REFERENCE</b><b>SIZE</b><b>THICKNESS</b><b>FOLDABLE</b><i>KSFG08-1224-16</i><i>2400 X 1220mm</i><i>1.6mm</i><i>Yes</i><span class="note">*CHECK AVAILABILITY</span></div></div>
      <div class="sw"><span class="chip" style="--c:#ee7a22">FEVE GLOSS<br>ORANGE</span><span class="under">MATTE WHITE<br>UNDERCOAT</span><div class="spec"><b>REFERENCE</b><b>SIZE</b><b>THICKNESS</b><b>FOLDABLE</b><i>KSFG09-1224-16</i><i>2400 X 1220mm</i><i>1.6mm</i><i>Yes</i></div></div>
      <div class="sw"><span class="chip" style="--c:#f08c2e">FEVE GLOSS<br>PUMPKIN</span><span class="under">MATTE WHITE<br>UNDERCOAT</span><div class="spec"><b>REFERENCE</b><b>SIZE</b><b>THICKNESS</b><b>FOLDABLE</b><i>KSFG10-1224-16</i><i>2400 X 1220mm</i><i>1.6mm</i><i>Yes</i><span class="note">*CHECK AVAILABILITY</span></div></div>
      <div class="sw"><span class="chip" style="--c:#1d2550">FEVE GLOSS<br>NAVY BLUE</span><span class="under">MATTE WHITE<br>UNDERCOAT</span><div class="spec"><b>REFERENCE</b><b>SIZE</b><b>THICKNESS</b><b>FOLDABLE</b><i>KSFG11-1224-16</i><i>2400 X 1220mm</i><i>1.6mm</i><i>Yes</i></div></div>
    </div>
  </div>

  <div class="panel">
    <div class="swatches swatches--tight mid-list">
      <div class="sw"><span class="chip" style="--c:#1d6f8e">FEVE GLOSS<br>LAGOON</span><span class="under">MATTE WHITE<br>UNDERCOAT</span><div class="spec"><b>REFERENCE</b><b>SIZE</b><b>THICKNESS</b><b>FOLDABLE</b><i>KSFG12-1224-16</i><i>2400 X 1220mm</i><i>1.6mm</i><i>Yes</i></div></div>
      <div class="sw"><span class="chip" style="--c:#28315f">FEVE GLOSS<br>GALAXY</span><span class="under">MATTE WHITE<br>UNDERCOAT</span><div class="spec"><b>REFERENCE</b><b>SIZE</b><b>THICKNESS</b><b>FOLDABLE</b><i>KSFG13-1224-16</i><i>2400 X 1220mm</i><i>1.6mm</i><i>Yes</i></div></div>
      <div class="sw"><span class="chip" style="--c:#1aa3b0">FEVE GLOSS<br>TURQUOISE</span><span class="under">MATTE WHITE<br>UNDERCOAT</span><div class="spec"><b>REFERENCE</b><b>SIZE</b><b>THICKNESS</b><b>FOLDABLE</b><i>KSFG14-1224-16</i><i>2400 X 1220mm</i><i>1.6mm</i><i>Yes</i><span class="note">*CHECK AVAILABILITY</span></div></div>
      <div class="sw"><span class="chip" style="--c:#1fa33a">FEVE GLOSS<br>GREEN</span><span class="under">MATTE WHITE<br>UNDERCOAT</span><div class="spec"><b>REFERENCE</b><b>SIZE</b><b>THICKNESS</b><b>FOLDABLE</b><i>KSFG15-1224-16</i><i>2400 X 1220mm</i><i>1.6mm</i><i>Yes</i><span class="note">*CHECK AVAILABILITY</span></div></div>
      <div class="sw"><span class="chip lt" style="--c:#e8dcae">FEVE GLOSS<br>IVORY</span><span class="under">MATTE WHITE<br>UNDERCOAT</span><div class="spec"><b>REFERENCE</b><b>SIZE</b><b>THICKNESS</b><b>FOLDABLE</b><i>KSFG16-1224-16</i><i>2400 X 1220mm</i><i>1.6mm</i><i>Yes</i></div></div>
      <div class="sw"><span class="chip" style="--c:#1f8a4a">FEVE GLOSS<br>EMERALD</span><span class="under">MATTE WHITE<br>UNDERCOAT</span><div class="spec"><b>REFERENCE</b><b>SIZE</b><b>THICKNESS</b><b>FOLDABLE</b><i>KSFG17-1224-16</i><i>2400 X 1220mm</i><i>1.6mm</i><i>Yes</i></div></div>
      <div class="sw"><span class="chip" style="--c:#5cb84a">FEVE GLOSS<br>APPLE GREEN</span><span class="under">MATTE WHITE<br>UNDERCOAT</span><div class="spec"><b>REFERENCE</b><b>SIZE</b><b>THICKNESS</b><b>FOLDABLE</b><i>KSFG18-1224-16</i><i>2400 X 1220mm</i><i>1.6mm</i><i>Yes</i></div></div>
      <div class="sw"><span class="chip" style="--c:#d4322a">FEVE GLOSS<br>WARM RED</span><span class="under">MATTE WHITE<br>UNDERCOAT</span><div class="spec"><b>REFERENCE</b><b>SIZE</b><b>THICKNESS</b><b>FOLDABLE</b><i>KSFG19-1224-16</i><i>2400 X 1220mm</i><i>1.6mm</i><i>Yes</i></div></div>
      <div class="sw"><span class="chip" style="--c:#f0b01c">FEVE GLOSS<br>MUSTARD</span><span class="under">MATTE WHITE<br>UNDERCOAT</span><div class="spec"><b>REFERENCE</b><b>SIZE</b><b>THICKNESS</b><b>FOLDABLE</b><i>KSFG20-1224-16</i><i>2400 X 1220mm</i><i>1.6mm</i><i>Yes</i><span class="note">*CHECK AVAILABILITY</span></div></div>
      <div class="sw"><span class="chip" style="--c:#6a3aa0">FEVE GLOSS<br>VIOLET</span><span class="under">MATTE WHITE<br>UNDERCOAT</span><div class="spec"><b>REFERENCE</b><b>SIZE</b><b>THICKNESS</b><b>FOLDABLE</b><i>KSFG21-1224-16</i><i>2400 X 1220mm</i><i>1.6mm</i><i>Yes</i><span class="note">*CHECK AVAILABILITY</span></div></div>
      <div class="sw"><span class="chip" style="--c:#8cc43c">FEVE GLOSS<br>LIME GREEN</span><span class="under">MATTE WHITE<br>UNDERCOAT</span><div class="spec"><b>REFERENCE</b><b>SIZE</b><b>THICKNESS</b><b>FOLDABLE</b><i>KSFG22-1224-16</i><i>2400 X 1220mm</i><i>1.6mm</i><i>Yes</i></div></div>
      <div class="sw"><span class="chip" style="--c:#3bb56a">FEVE GLOSS<br>SPRING GREEN</span><span class="under">MATTE WHITE<br>UNDERCOAT</span><div class="spec"><b>REFERENCE</b><b>SIZE</b><b>THICKNESS</b><b>FOLDABLE</b><i>KSFG23-1224-16</i><i>2400 X 1220mm</i><i>1.6mm</i><i>Yes</i></div></div>
      <div class="sw"><span class="chip" style="--c:#d0246e">FEVE GLOSS<br>FUCHSIA</span><span class="under">MATTE WHITE<br>UNDERCOAT</span><div class="spec"><b>REFERENCE</b><b>SIZE</b><b>THICKNESS</b><b>FOLDABLE</b><i>KSFG24-1224-16</i><i>2400 X 1220mm</i><i>1.6mm</i><i>Yes</i></div></div>
      <div class="sw"><span class="chip" style="--c:#a9203a">FEVE GLOSS<br>PLUM RED</span><span class="under">MATTE WHITE<br>UNDERCOAT</span><div class="spec"><b>REFERENCE</b><b>SIZE</b><b>THICKNESS</b><b>FOLDABLE</b><i>KSFG25-1224-16</i><i>2400 X 1220mm</i><i>1.6mm</i><i>Yes</i></div></div>
      <div class="sw"><span class="chip" style="--c:#e783b2">FEVE GLOSS<br>PINK</span><span class="under">MATTE WHITE<br>UNDERCOAT</span><div class="spec"><b>REFERENCE</b><b>SIZE</b><b>THICKNESS</b><b>FOLDABLE</b><i>KSFG26-1224-16</i><i>2400 X 1220mm</i><i>1.6mm</i><i>Yes</i><span class="note">*CHECK AVAILABILITY</span></div></div>
      <div class="sw"><span class="chip" style="--c:#4a5058">FEVE GLOSS<br>STEEL GREY</span><span class="under">MATTE WHITE<br>UNDERCOAT</span><div class="spec"><b>REFERENCE</b><b>SIZE</b><b>THICKNESS</b><b>FOLDABLE</b><i>KSFG27-1224-16</i><i>2400 X 1220mm</i><i>1.6mm</i><i>Yes</i></div></div>
      <div class="sw"><span class="chip" style="--c:#3ab8a0">FEVE GLOSS<br>MINT</span><span class="under">MATTE WHITE<br>UNDERCOAT</span><div class="spec"><b>REFERENCE</b><b>SIZE</b><b>THICKNESS</b><b>FOLDABLE</b><i>KSFG28-1224-16</i><i>2400 X 1220mm</i><i>1.6mm</i><i>Yes</i><span class="note">*CHECK AVAILABILITY</span></div></div>
      <div class="sw"><span class="chip" style="--c:#1a7f7a">FEVE GLOSS<br>TEAL</span><span class="under">MATTE WHITE<br>UNDERCOAT</span><div class="spec"><b>REFERENCE</b><b>SIZE</b><b>THICKNESS</b><b>FOLDABLE</b><i>KSFG29-1224-16</i><i>2400 X 1220mm</i><i>1.6mm</i><i>Yes</i><span class="note">*CHECK AVAILABILITY</span></div></div>
      <div class="sw"><span class="chip" style="--c:#6e4a32">FEVE GLOSS<br>MILK CHOCOLATE</span><span class="under">MATTE WHITE<br>UNDERCOAT</span><div class="spec"><b>REFERENCE</b><b>SIZE</b><b>THICKNESS</b><b>FOLDABLE</b><i>KSFG30-1224-16</i><i>2400 X 1220mm</i><i>1.6mm</i><i>Yes</i><span class="note">*CHECK AVAILABILITY</span></div></div>
      <div class="sw"><span class="chip lt" style="--c:#f2e14a">FEVE GLOSS<br>LEMON MERINGUE</span><span class="under">MATTE WHITE<br>UNDERCOAT</span><div class="spec"><b>REFERENCE</b><b>SIZE</b><b>THICKNESS</b><b>FOLDABLE</b><i>KSFG31-1224-16</i><i>2400 X 1220mm</i><i>1.6mm</i><i>Yes</i><span class="note">*CHECK AVAILABILITY</span></div></div>
      <div class="sw"><span class="chip" style="--c:#8cc0e6">FEVE GLOSS<br>BABY BLUE</span><span class="under">MATTE WHITE<br>UNDERCOAT</span><div class="spec"><b>REFERENCE</b><b>SIZE</b><b>THICKNESS</b><b>FOLDABLE</b><i>KSFG32-1224-16</i><i>2400 X 1220mm</i><i>1.6mm</i><i>Yes</i><span class="note">*CHECK AVAILABILITY</span></div></div>
      <div class="sw"><span class="chip" style="--c:#1c4fa0">FEVE GLOSS<br>PATRIOTIC BLUE</span><span class="under">MATTE WHITE<br>UNDERCOAT</span><div class="spec"><b>REFERENCE</b><b>SIZE</b><b>THICKNESS</b><b>FOLDABLE</b><i>KSFG33-1224-16</i><i>2400 X 1220mm</i><i>1.6mm</i><i>Yes</i><span class="note">*CHECK AVAILABILITY</span></div></div>
      <div class="sw"><span class="chip" style="--c:#6f8a4a">FEVE GLOSS<br>OLIVE GREEN</span><span class="under">MATTE WHITE<br>UNDERCOAT</span><div class="spec"><b>REFERENCE</b><b>SIZE</b><b>THICKNESS</b><b>FOLDABLE</b><i>KSFG34-1224-16</i><i>2400 X 1220mm</i><i>1.6mm</i><i>Yes</i><span class="note">*CHECK AVAILABILITY</span></div></div>
      <div class="sw"><span class="chip" style="--c:#5c6168">FEVE GLOSS<br>IRON GREY</span><span class="under">MATTE WHITE<br>UNDERCOAT</span><div class="spec"><b>REFERENCE</b><b>SIZE</b><b>THICKNESS</b><b>FOLDABLE</b><i>KSFG35-1224-16</i><i>2400 X 1220mm</i><i>1.6mm</i><i>Yes</i></div></div>
      <div class="sw"><span class="chip" style="--c:#9b9a97">FEVE GLOSS<br>WARM GREY</span><span class="under">MATTE WHITE<br>UNDERCOAT</span><div class="spec"><b>REFERENCE</b><b>SIZE</b><b>THICKNESS</b><b>FOLDABLE</b><i>KSFG36-1224-16</i><i>2400 X 1220mm</i><i>1.6mm</i><i>Yes</i></div></div>
      <div class="sw"><span class="chip" style="--c:#8c8e90">FEVE GLOSS<br>SMOKEY GREY</span><span class="under">MATTE WHITE<br>UNDERCOAT</span><div class="spec"><b>REFERENCE</b><b>SIZE</b><b>THICKNESS</b><b>FOLDABLE</b><i>KSFG37-1224-16</i><i>2400 X 1220mm</i><i>1.6mm</i><i>Yes</i></div></div>
    </div>
  </div>

  <div class="panel">
    <div class="swatches swatches--tight right-top">
      <div class="sw"><span class="chip" style="--c:#b8a890">FEVE GLOSS<br>LATTE</span><span class="under">MATTE WHITE<br>UNDERCOAT</span><div class="spec"><b>REFERENCE</b><b>SIZE</b><b>THICKNESS</b><b>FOLDABLE</b><i>KSFG38-1224-16</i><i>2400 X 1220mm</i><i>1.6mm</i><i>Yes</i></div></div>
      <div class="sw"><span class="chip" style="--c:#8d8578">FEVE GLOSS<br>STONE</span><span class="under">MATTE WHITE<br>UNDERCOAT</span><div class="spec"><b>REFERENCE</b><b>SIZE</b><b>THICKNESS</b><b>FOLDABLE</b><i>KSFG39-1224-16</i><i>2400 X 1220mm</i><i>1.6mm</i><i>Yes</i><span class="note">*CHECK AVAILABILITY</span></div></div>
      <div class="sw"><span class="chip" style="--c:#6a5547">FEVE GLOSS<br>MOCHA</span><span class="under">MATTE WHITE<br>UNDERCOAT</span><div class="spec"><b>REFERENCE</b><b>SIZE</b><b>THICKNESS</b><b>FOLDABLE</b><i>KSFG40-1224-16</i><i>2400 X 1220mm</i><i>1.6mm</i><i>Yes</i><span class="note">*CHECK AVAILABILITY</span></div></div>
      <div class="sw"><span class="chip" style="--c:#4a2c3f">FEVE GLOSS<br>AUBERGINE</span><span class="under">MATTE WHITE<br>UNDERCOAT</span><div class="spec"><b>REFERENCE</b><b>SIZE</b><b>THICKNESS</b><b>FOLDABLE</b><i>KSFG41-1224-16</i><i>2400 X 1220mm</i><i>1.6mm</i><i>Yes</i><span class="note">*CHECK AVAILABILITY</span></div></div>
      <div class="sw"><span class="chip" style="--c:#3a2f66">FEVE GLOSS<br>MIDNIGHT PURPLE</span><span class="under">MATTE WHITE<br>UNDERCOAT</span><div class="spec"><b>REFERENCE</b><b>SIZE</b><b>THICKNESS</b><b>FOLDABLE</b><i>KSFG42-1224-16</i><i>2400 X 1220mm</i><i>1.6mm</i><i>Yes</i><span class="note">*CHECK AVAILABILITY</span></div></div>
      <div class="sw"><span class="chip" style="--c:#f08a22">FEVE GLOSS<br>TANGERINE</span><span class="under">MATTE WHITE<br>UNDERCOAT</span><div class="spec"><b>REFERENCE</b><b>SIZE</b><b>THICKNESS</b><b>FOLDABLE</b><i>KSFG43-1224-16</i><i>2400 X 1220mm</i><i>1.6mm</i><i>Yes</i><span class="note">*CHECK AVAILABILITY</span></div></div>
      <div class="sw"><span class="chip" style="--c:#8a8c8e">FEVE GLOSS<br>ASH</span><span class="under">MATTE WHITE<br>UNDERCOAT</span><div class="spec"><b>REFERENCE</b><b>SIZE</b><b>THICKNESS</b><b>FOLDABLE</b><i>KSFG44-1224-16</i><i>2400 X 1220mm</i><i>1.6mm</i><i>Yes</i><span class="note">*CHECK AVAILABILITY</span></div></div>
      <div class="sw"><span class="chip lt" style="--c:#dcd5c2">FEVE GLOSS<br>CREAM</span><span class="under">MATTE WHITE<br>UNDERCOAT</span><div class="spec"><b>REFERENCE</b><b>SIZE</b><b>THICKNESS</b><b>FOLDABLE</b><i>KSFG45-1224-16</i><i>2400 X 1220mm</i><i>1.6mm</i><i>Yes</i><span class="note">*CHECK AVAILABILITY</span></div></div>
      <div class="sw"><span class="chip" style="--c:#7a2e22">FEVE GLOSS<br>RUST</span><span class="under">MATTE WHITE<br>UNDERCOAT</span><div class="spec"><b>REFERENCE</b><b>SIZE</b><b>THICKNESS</b><b>FOLDABLE</b><i>KSFG46-1224-16</i><i>2400 X 1220mm</i><i>1.6mm</i><i>Yes</i><span class="note">*CHECK AVAILABILITY</span></div></div>
      <div class="sw"><span class="chip" style="--c:#1e3a9a">FEVE ROYAL<br>BLUE</span><span class="under">MATTE WHITE<br>UNDERCOAT</span><div class="spec"><b>REFERENCE</b><b>SIZE</b><b>THICKNESS</b><b>FOLDABLE</b><i>KSFG47-1224-16</i><i>2400 X 1220mm</i><i>1.6mm</i><i>Yes</i><span class="note">*CHECK AVAILABILITY</span></div></div>
      <div class="sw"><span class="chip" style="--c:#6b3ca8">FEVE<br>VIOLET</span><span class="under">MATTE WHITE<br>UNDERCOAT</span><div class="spec"><b>REFERENCE</b><b>SIZE</b><b>THICKNESS</b><b>FOLDABLE</b><i>KSFG48-1224-16</i><i>2400 X 1220mm</i><i>1.6mm</i><i>Yes</i><span class="note">*CHECK AVAILABILITY</span></div></div>
      <div class="sw"><span class="chip" style="--c:#7a2aa0">FEVE<br>PURPLE</span><span class="under">MATTE WHITE<br>UNDERCOAT</span><div class="spec"><b>REFERENCE</b><b>SIZE</b><b>THICKNESS</b><b>FOLDABLE</b><i>KSFG49-1224-16</i><i>2400 X 1220mm</i><i>1.6mm</i><i>Yes</i><span class="note">*CHECK AVAILABILITY</span></div></div>
      <div class="sw"><span class="chip" style="--c:#b21a6a">FEVE<br>MULBERRY</span><span class="under">MATTE WHITE<br>UNDERCOAT</span><div class="spec"><b>REFERENCE</b><b>SIZE</b><b>THICKNESS</b><b>FOLDABLE</b><i>KSFG50-1224-16</i><i>2400 X 1220mm</i><i>1.6mm</i><i>Yes</i><span class="note">*CHECK AVAILABILITY</span></div></div>
    </div>

    <h3 class="metal-head">METALLICS &amp; PEARLS 1.6MM</h3>

    <div class="swatches swatches--tight right-bottom">
      <div class="sw"><span class="chip" style="--c:#b8a27a">FEVE METALLIC<br>CHAMPAGNE</span><span class="under">MATTE WHITE<br>UNDERCOAT</span><div class="spec"><b>REFERENCE</b><b>SIZE</b><b>THICKNESS</b><b>FOLDABLE</b><i>KSFM01-1224-16</i><i>2400 X 1220mm</i><i>1.6mm</i><i>Yes</i></div></div>
      <div class="sw"><span class="chip" style="--c:#c8a040">FEVE METALLIC<br>GOLD</span><span class="under">MATTE WHITE<br>UNDERCOAT</span><div class="spec"><b>REFERENCE</b><b>SIZE</b><b>THICKNESS</b><b>FOLDABLE</b><i>KSFM02-1224-16</i><i>2400 X 1220mm</i><i>1.6mm</i><i>Yes</i></div></div>
      <div class="sw"><span class="chip" style="--c:#c8c8c8">FEVE METALLIC<br>FLASH SILVER</span><span class="under">MATTE WHITE<br>UNDERCOAT</span><div class="spec"><b>REFERENCE</b><b>SIZE</b><b>THICKNESS</b><b>FOLDABLE</b><i>KSFM03-1224-16</i><i>2400 X 1220mm</i><i>1.6mm</i><i>Yes</i></div></div>
      <div class="sw"><span class="chip" style="--c:#a8a8a8">FEVE METALLIC<br>SILVER</span><span class="under">MATTE WHITE<br>UNDERCOAT</span><div class="spec"><b>REFERENCE</b><b>SIZE</b><b>THICKNESS</b><b>FOLDABLE</b><i>KSFM04-1224-16</i><i>2400 X 1220mm</i><i>1.6mm</i><i>Yes</i></div></div>
      <div class="sw"><span class="chip" style="--c:#505050">FEVE METALLIC<br>CHARCOAL</span><span class="under">MATTE WHITE<br>UNDERCOAT</span><div class="spec"><b>REFERENCE</b><b>SIZE</b><b>THICKNESS</b><b>FOLDABLE</b><i>KSFM05-1224-16</i><i>2400 X 1220mm</i><i>1.6mm</i><i>Yes</i></div></div>
      <div class="sw"><span class="chip" style="--c:#9a9a9a">FEVE METALLIC<br>SILVER</span><span class="under">MATTE WHITE<br>UNDERCOAT</span><div class="spec"><b>REFERENCE</b><b>SIZE</b><b>THICKNESS</b><b>FOLDABLE</b><i>KSFM06-1224-16</i><i>2400 X 1220mm</i><i>1.6mm</i><i>Yes</i><span class="note">*CHECK AVAILABILITY</span></div></div>
      <div class="sw"><span class="chip lt" style="--c:#e8e8e8">FEVE PEARL<br>WHITE</span><span class="under">MATTE WHITE<br>UNDERCOAT</span><div class="spec"><b>REFERENCE</b><b>SIZE</b><b>THICKNESS</b><b>FOLDABLE</b><i>KSFM07-1224-16</i><i>2400 X 1220mm</i><i>1.6mm</i><i>Yes</i><span class="note">*CHECK AVAILABILITY</span></div></div>
      <div class="sw"><span class="chip" style="--c:#c9b9a0">FEVE PEARL<br>LATTE</span><span class="under">MATTE WHITE<br>UNDERCOAT</span><div class="spec"><b>REFERENCE</b><b>SIZE</b><b>THICKNESS</b><b>FOLDABLE</b><i>KSFM08-1224-16</i><i>2400 X 1220mm</i><i>1.6mm</i><i>Yes</i><span class="note">*CHECK AVAILABILITY</span></div></div>
      <div class="sw"><span class="chip" style="--c:#8a9aa8">FEVE PEARL<br>OCEAN GREY</span><span class="under">MATTE WHITE<br>UNDERCOAT</span><div class="spec"><b>REFERENCE</b><b>SIZE</b><b>THICKNESS</b><b>FOLDABLE</b><i>KSFM09-1224-16</i><i>2400 X 1220mm</i><i>1.6mm</i><i>Yes</i><span class="note">*CHECK AVAILABILITY</span></div></div>
      <div class="sw"><span class="chip" style="--c:#8898b0">FEVE PEARL<br>BLUE GREY</span><span class="under">MATTE WHITE<br>UNDERCOAT</span><div class="spec"><b>REFERENCE</b><b>SIZE</b><b>THICKNESS</b><b>FOLDABLE</b><i>KSFM10-1224-16</i><i>2400 X 1220mm</i><i>1.6mm</i><i>Yes</i><span class="note">*CHECK AVAILABILITY</span></div></div>
      <div class="sw"><span class="chip" style="--c:#1a1a1a">FEVE METALLIC<br>BLACK</span><span class="under">MATTE WHITE<br>UNDERCOAT</span><div class="spec"><b>REFERENCE</b><b>SIZE</b><b>THICKNESS</b><b>FOLDABLE</b><i>KSFM11-1224-16</i><i>2400 X 1220mm</i><i>1.6mm</i><i>Yes</i><span class="note">*CHECK AVAILABILITY</span></div></div>
      <div class="sw"><span class="chip" style="--c:#b06a3a">FEVE PEARL<br>COPPER</span><span class="under">MATTE WHITE<br>UNDERCOAT</span><div class="spec"><b>REFERENCE</b><b>SIZE</b><b>THICKNESS</b><b>FOLDABLE</b><i>KSFM12-1224-16</i><i>2400 X 1220mm</i><i>1.6mm</i><i>Yes</i><span class="note">*CHECK AVAILABILITY</span></div></div>
      <div class="sw"><span class="chip" style="--c:#b8944a">FEVE METALLIC<br>BRASS GOLD</span><span class="under">MATTE WHITE<br>UNDERCOAT</span><div class="spec"><b>REFERENCE</b><b>SIZE</b><b>THICKNESS</b><b>FOLDABLE</b><i>KSFM13-1224-16</i><i>2400 X 1220mm</i><i>1.6mm</i><i>Yes</i><span class="note">*CHECK AVAILABILITY</span></div></div>
    </div>
  </div>
</section>

</body>
</html>
```